Real Estate Web Page Redesign

We are a small town real estate agency in need of a web site redesign. To give you a little background on our agency…our target is middle income households and farmers. Our staff includes real estate agents and an auctioneer. We’ve been in business since 1997. We handle residential, commercial, recreational land and farmland.
Our current web site design is outdated and needs a more modern look. We are open to all design ideas but would want them to reflect our small town rural tradition and heritage.
The functionality and features of the site will remain the same. Your design will have to accommodate the existing features on the site. I have a programmer who will take the design you provide and retrofit the existing site functionality with it.
The deliverable will be a .psd file that can be converted to html for a site template. (We will do the conversion.)
The existing site is at:
http://www.tomwendellhomesales.example/home.asp
Please take time to visit the site and note the current functionality the site has: property search, real estate news feed, mortgage rate feed, listings, navigation bar will need to handle existing links and expand to handle other future page links. The template provided will need to accommodate these features.
The current page logo can be used in the design or we are open to a redesign of that as well if needed to go with the design better.
Updates
Project Deadline Extended
Reason: Haven't had anything satisfactory yet.
Target Market(s)
Middle income households and farmers looking for the services of a real estate agent or auctioneer.
Industry/Entity Type
Real Estate
Look and feel

```html
<!DOCTYPE html>
<html lang="en">
<head>
<meta charset="utf-8">
<title>Wendell Real Estate and Land Company</title>
<link href="https://fonts.googleapis.com/css2?family=Arimo:ital,wght@0,400;0,700;1,700&family=PT+Serif&display=swap" rel="stylesheet">
<style>
:root{
  --sky-top:#3f6a8c; --sky-mid:#5b94c2; --sky-light:#8ab8dc;
  --page:#ffffff; --panel:#eceef0;
  --brown:#8a5526; --ink:#4a4a4a;
  --blue:#2a8fc9; --blue-deep:#1a5fd6; --cyan:#2cb6ec;
  --orange:#ee6d12; --orange-light:#f79a3e;
  --footer:#47484c; --footer-dark:#2f3035; --slate:#5c6280; --slate-text:#9aa3c8;
}
*{box-sizing:border-box;margin:0;padding:0}
html,body{width:1180px;height:1200px;overflow:hidden}
body{font-family:"Arimo",Arial,sans-serif;color:var(--ink);background:var(--footer)}
.stage{position:absolute;left:0;top:0;width:1024px;height:1041.5px;transform:scale(1.15234,1.1522);transform-origin:0 0;
  background:linear-gradient(180deg,var(--sky-top) 0,var(--sky-top) 30px,var(--sky-mid) 30px,var(--sky-light) 500px,var(--sky-mid) 822px,var(--footer) 822px)}
.abs{position:absolute}
.page{left:78px;top:29px;width:892px;height:793px;background:var(--page);border-radius:8px}
.brand{left:137px;top:72px;font-weight:700;font-size:34px;color:var(--brown);line-height:1;letter-spacing:.3px}
.brand span{display:block;font-size:22px;margin-left:212px;margin-top:2px}
.nav{left:171px;top:147px;width:759px;height:41px;border-radius:10px;border:1px solid #cfcfcf;
  background:linear-gradient(#fafafa,#e6e6e6 60%,#d3d3d3);box-shadow:0 4px 4px rgba(0,0,0,.12);display:flex;align-items:center;padding-left:16px}
.nav a{font-size:14px;color:#555;text-decoration:none;padding:0 16px;border-right:1px solid #ccc;line-height:26px;display:flex;align-items:center;gap:8px}
.nav a:last-child{border:none}
.hero-band{left:78px;top:208px;width:892px;height:240px;background:#f2f3f4}
.hero-art{left:86px;top:213px;width:299px;height:297px;border-radius:4px;background:linear-gradient(180deg,#c9d6ee 0%,#d9c29a 50%,#c7a57a 80%,#b98a7a 100%)}
.card{background:linear-gradient(#f5f6f7,#e3e6e9);border-radius:6px}
.finder{left:396px;top:224px;width:537px;height:117px}
.finder h2{position:absolute;left:172px;top:4px;font-size:25px;font-weight:400;color:#333;letter-spacing:-.5px}
.finder h2 b{color:var(--blue)}
.select{position:absolute;width:132px;height:22px;border:1px solid #b9b9b9;background:#f4f4f4}
.select::after{content:"";position:absolute;right:3px;top:3px;width:13px;height:14px;border:1px solid #aaa;background:linear-gradient(#fff,#ddd)}
.select::before{content:"";position:absolute;right:7px;top:9px;border:3px solid transparent;border-top:4px solid #333;z-index:1}
.search-btn{position:absolute;left:354px;top:58px;width:152px;height:39px;border-radius:5px;border:none;color:#fff;font:700 15px "Arimo",Arial,sans-serif;letter-spacing:.5px;text-align:left;padding-left:28px;
  background:linear-gradient(90deg,transparent 118px,#c9500a 118px),linear-gradient(var(--orange-light),var(--orange));box-shadow:0 2px 3px rgba(0,0,0,.3)}
.rates{left:396px;top:354px;width:537px;height:151px}
.rates h3{position:absolute;left:0;width:100%;top:10px;text-align:center;font-size:14px;color:var(--blue);letter-spacing:.3px}
.rates hr{position:absolute;left:27px;top:29px;width:489px;border:none;border-top:1px solid #7aa6d8}
.rates h4{position:absolute;left:31px;top:46px;font-size:11.5px;font-weight:400;color:#2a6fd0}
.rate-table{position:absolute;left:104px;top:69px;border-collapse:collapse;font-size:11px;color:#333}
.rate-table td{padding:0;line-height:14px}
.rate-table .dash{color:#888;padding:0 14px 0 10px;letter-spacing:-1px}
.rate-table .num{text-align:right;width:50px}
.rate-table .chg{text-align:right;width:62px}
.lower{left:83px;top:510px;width:887px;height:287px;background:var(--panel);border-radius:6px}
.tab{left:73px;top:527px;width:160px;height:25px;background:linear-gradient(#9b9b9b,#6f6f6f);color:#fff;font-weight:700;font-size:13px;padding:5px 0 0 24px}
.tab::after{content:"";position:absolute;left:0;top:25px;border-left:10px solid transparent;border-top:10px solid #3b3b3b}
.listing-photo{width:119px;height:88px;background:linear-gradient(180deg,#cfe3ea 0,#6f9a55 45%,#4e7d36 75%,#b9b2a2 100%)}
.listing-title{font-family:"PT Serif",Georgia,serif;font-size:13.5px;color:#444}
.price{font-family:"PT Serif",Georgia,serif;font-size:16px;color:#444;letter-spacing:.5px}
.more{width:68px;height:20px;background:var(--cyan);color:#fff;font-size:13px;text-align:center;line-height:20px}
.divider{left:443px;top:532px;width:1px;height:237px;background:#888}
.portrait{left:461px;top:544px;width:114px;height:136px;border:2px solid #2f6b2a;background:linear-gradient(180deg,#7a9a6a,#6b7f8f 55%,#3b4f7a)}
.welcome{font-size:12.2px;line-height:15.8px;color:#555;letter-spacing:.45px}
.welcome strong{font-style:italic;font-size:28px;color:var(--blue-deep);letter-spacing:.5px;font-weight:700}
.mail-box,.follow-box{background:var(--slate);border-radius:8px}
.mail-box{left:43px;top:871px;width:305px;height:117px}
.notch{position:absolute;top:-17px;width:0;height:0;border-left:18px solid var(--slate);border-top:17px solid transparent}
.mail-box h5,.follow-box h5{position:absolute;color:#fff;font-size:14px;font-weight:700}
.email-input{position:absolute;left:34px;top:44px;width:244px;height:38px;background:#bfbfbf;color:#222;font-size:13px;padding:12px 0 0 14px}
.go{position:absolute;left:226px;top:89px;width:51px;height:35px;border-radius:6px;background:linear-gradient(#ddd,#b5b5b5);color:#222;font-weight:700;font-size:13px;text-align:center;line-height:35px}
.contact{left:381px;top:825px;width:289px;height:216px;background:var(--footer-dark);overflow:hidden}
.contact-label{color:#fff;font-weight:700;font-size:14px}
.contact-value{color:var(--slate-text);font-size:14px;white-space:nowrap}
.address{left:403px;top:940px;color:#ddd;font-weight:700;font-size:12.5px;line-height:15.6px;letter-spacing:.3px;font-style:normal}
.follow-box{left:688px;top:879px;width:305px;height:116px}
.social{position:absolute;top:62px;width:31px;height:31px;border-radius:4px}
</style>
</head>
<body>
<div class="stage">
  <div class="abs page"></div>

  <div class="abs brand">Wendell Real Estate<span>and Land Company</span></div>

  <nav class="abs nav">
    <a href="#"><svg width="17" height="16" viewBox="0 0 17 16"><path d="M8.5 1 1 8h2.5v7h4v-4h2v4h4V8H16z" fill="#777"/></svg>Home</a>
    <a href="#">About</a>
    <a href="#">&nbsp;&nbsp;Services</a>
    <a href="#">Calculator</a>
    <a href="#">Contact</a>
    <a href="#" style="padding-left:9px">Open Houses</a>
  </nav>

  <div class="abs hero-band"></div>
  <div class="abs hero-art" role="img" aria-label="Illustration of a family house with a blue roof and red front steps"></div>

  <section class="abs card finder">
    <h2><b>Find</b> a Home <svg width="24" height="24" viewBox="0 0 24 24" style="vertical-align:-2px"><circle cx="9" cy="9" r="6.5" fill="#d8eaf7" stroke="#5a8fb5" stroke-width="2"/><path d="M14 14l7 7" stroke="#666" stroke-width="3.5" stroke-linecap="round"/></svg></h2>
    <div class="select" style="left:31px;top:48px"></div>
    <div class="select" style="left:187px;top:46px"></div>
    <div class="select" style="left:31px;top:80px"></div>
    <div class="select" style="left:187px;top:77px"></div>
    <button class="search-btn">SEARCH<svg width="18" height="18" viewBox="0 0 18 18" style="position:absolute;right:10px;top:11px"><circle cx="7" cy="7" r="5" fill="none" stroke="#fff" stroke-width="2"/><path d="M11 11l5 5" stroke="#fff" stroke-width="2.5" stroke-linecap="round"/></svg></button>
  </section>

  <section class="abs card rates">
    <h3>MORTGAGE RATES</h3>
    <hr>
    <h4>NATIONAL &nbsp;AVERAGES</h4>
    <table class="rate-table">
      <tr><td>30 YR FIXED</td><td class="dash">---------------------------------</td><td class="num">4.56%</td><td class="chg">-0.01%</td></tr>
      <tr><td>15 YR FIXED</td><td class="dash">---------------------------------</td><td class="num">4.03%</td><td class="chg">-0.03%</td></tr>
      <tr><td>1 YR ARM</td><td class="dash">---------------------------------</td><td class="num">3.70%</td><td class="chg">-0.04%</td></tr>
      <tr><td>&nbsp;FED PRIME</td><td class="dash">---------------------------------</td><td class="num">3.25%</td><td class="chg">0.00%</td></tr>
      <tr><td>&nbsp;30 YR TRES</td><td class="dash">---------------------------------</td><td class="num">4.08%</td><td class="chg">0.00%</td></tr>
    </table>
  </section>

  <div class="abs lower"></div>
  <div class="abs tab">Premier Listing</div>

  <div class="abs listing-photo" style="left:98px;top:574px" role="img" aria-label="Photo of a two-storey house among trees"></div>
  <div class="abs listing-title" style="left:232px;top:590px">4 Bedroom , Cedar Hill</div>
  <div class="abs price" style="left:232px;top:611px">$130,00</div>
  <div class="abs more" style="left:225px;top:643px">More</div>

  <div class="abs listing-photo" style="left:98px;top:689px" role="img" aria-label="Photo of a two-storey house among trees"></div>
  <div class="abs listing-title" style="left:232px;top:699px">4 Bedroom , Cedar Hill</div>
  <div class="abs price" style="left:233px;top:725px">$130,00</div>
  <div class="abs more" style="left:225px;top:758px">More</div>

  <div class="abs divider"></div>
  <div class="abs portrait" role="img" aria-label="Portrait of the broker"></div>

  <p class="abs welcome" style="left:587px;top:532px;width:370px"><strong>Welcome</strong> to Wendell Real Estate and Land Company's web site. Your visit here will make it easy for you to find the real estate you are seeking by using our simple search menu. Not only will you find area real estate listings, but also other items such as the latest mortgage rates and real estate news, and businesses that are associated with buying and selling homes and farmland. I will be servicing the needs of the people in the Alden, Cedar Hill, Milford, Oakton, Elmwood and all area communities.</p>
  <p class="abs welcome" style="left:459px;top:689px;width:496px">&nbsp;I have been in the real estate business since 1997 and have been a broker since 1999. I'm looking forward to marketing your property for "top dollar" or finding that "perfect" piece of property you desire whether it be residential, commercial, recreational, farmland (statewide), country property, or 1031 exchange. I am also a member of the Prairie Valley Multiple Listing Service.</p>

  <section class="abs mail-box">
    <span class="notch" style="left:277px"></span>
    <h5 style="left:39px;top:19px">Join our mailing list.</h5>
    <div class="email-input">E-mail Address</div>
    <div class="go">GO</div>
  </section>

  <section class="abs contact">
    <svg class="abs" style="left:70px;top:10px" width="31" height="31" viewBox="0 0 31 31"><rect width="31" height="31" rx="5" fill="#3f86c4"/><path d="M10 7c-2 1-3 3-2 6 2 5 6 9 11 11 3 1 5 0 6-2l-3-3-3 2c-3-1-5-4-6-6l2-3z" fill="#fff"/></svg>
    <div class="abs contact-label" style="left:126px;top:15px">PHONE</div>
    <div class="abs contact-value" style="left:126px;top:32px">555-0142</div>
    <svg class="abs" style="left:70px;top:62px" width="31" height="29" viewBox="0 0 31 29"><rect x="1" y="4" width="29" height="21" fill="#eee" stroke="#bbb"/><path d="M1 4l14.5 12L30 4" fill="none" stroke="#aaa" stroke-width="1.5"/></svg>
    <div class="abs contact-label" style="left:126px;top:66px">EMAIL</div>
    <div class="abs contact-value" style="left:126px;top:83px">hello@wendell.example</div>
  </section>
  <address class="abs address">Wendell Real Estate and Land Company<br>2180 N 300th Ave.<br>Milford, IL 61000<br>Fax: (309) 555-0187</address>

  <section class="abs follow-box">
    <span class="notch" style="left:277px"></span>
    <h5 style="left:23px;top:17px">Follow Us</h5>
    <span class="social" style="left:75px;background:#7fd3ec"></span>
    <span class="social" style="left:116px;background:#3f65b4"></span>
    <span class="social" style="left:157px;background:#f1f1f1"></span>
    <span class="social" style="left:197px;background:#2a7fb8"></span>
  </section>
</div>
</body>
</html>
```